Vantrel System Web Page Design

This project is to design 6 pages of a web based medical system for clinics, hospitals, drugs suppliers, general items suppliers, insurance company, laboratories and patients (basically all parties which could be involved in).We want the designs of the browser, button, icon and layout are based on Zeltor, which is user friendly, looks professional, simple and neat but with powerful functions. We have uploaded few pictures of another system, please do not copy its design because this is not what we are looking for, the pictures are for you to know the elements should be included in our pages. Vantrel web-base system, design 6 pages1. Login PageShould include the following elements-company id with input field-login id with input field-password with input field2. Main Page (Navigation page)Should include the following elements-Appointment-Consultation-Patient-Drugs inventory -General supplies inventory -Laboratory-Suppliers-Insurance-Reports 3. Appointment PageShould include all the the elements in the respective pictures plus the followings-Daily View, Weekly View, Monthly View buttons4. Consultation PageShould include all the the elements in the respective picture5. Patient Page5.1 General information Should include all the the elements in the respective picture5.2 medical history/lab reportsShould include all the the elements in the respective picture plus the followings-Notify patient button-Share report button.
Updated on 28 Nov:
Please stop using Harbor Suite in your designs which is not the name of our system. We have just rename our system to Vantrel, please take note.
We need the system to look professional not playful, do not use too many colors and playful icons.

```html
<!DOCTYPE html>
<html lang="en">
<head>
<meta charset="utf-8">
<title>Vantrel – Reports</title>
<link rel="stylesheet" href="https://fonts.googleapis.com/css2?family=Roboto:wght@300;400;700&display=swap">
<style>
:root{
  --brand:#1f5fad;
  --ink:#3a3a3a;
  --line:#c9c9c9;
  --soft-line:#f0f0f0;
  --sidebar-bg:#f8f8f8;
  --muted:#dcdcdc;
  --muted-text:#d0d0d0;
  --active-bg:#d3e0f0;
  --ghost-border:#d6e2f0;
  --ghost-text:#c5d5e8;
  --avatar:#c9ced6;
  --white:#ffffff;
}
*{margin:0;padding:0;box-sizing:border-box}
html,body{width:1200px;height:674px;overflow:hidden;background:var(--white);font-family:"Roboto",Arial,sans-serif;color:var(--ink)}
.app{position:relative;width:1200px;height:674px}
.topbar{position:absolute;left:0;top:0;width:1200px;height:81px;border-bottom:2px solid var(--line);background:var(--white)}
.brand{position:absolute;left:24px;top:22px;display:flex;align-items:center;gap:10px;color:var(--brand);font-size:26px;font-weight:400}
.brand-dot{width:26px;height:26px;border-radius:50%;background:var(--brand)}
.user{position:absolute;left:955px;top:12px;display:flex;align-items:center}
.avatar{width:58px;height:58px;border-radius:50%;background:var(--avatar)}
.user-name{margin-left:14px;font-size:16px;color:#222}
.user-caret{margin-left:34px}
.sidebar{position:absolute;left:0;top:83px;width:208px;height:591px;background:var(--sidebar-bg);border-right:1px solid var(--soft-line)}
.nav-item{position:absolute;left:0;width:208px;padding-left:33px;font-size:16px;font-weight:700;color:var(--muted);line-height:19px}
.nav-item.active{background:var(--active-bg);color:var(--white);height:30px;line-height:30px}
.select{position:absolute;top:114px;height:36px;border:1px solid var(--soft-line);border-radius:3px;font-size:15px;font-weight:300;color:var(--muted-text);padding:8px 9px}
.select svg{position:absolute;right:10px;top:13px}
.table{position:absolute;left:250px;top:175px;width:896px;height:369px;border:1px solid var(--soft-line);border-radius:3px}
.row{position:relative;height:31.2px;border-bottom:1px solid var(--soft-line);font-size:12.5px;font-weight:300;color:var(--muted-text);line-height:31px}
.row .name{position:absolute;left:16px}
.row .act{position:absolute;text-decoration:underline}
.scroll{position:absolute;left:1135px;top:384px;width:5px;height:88px;border-radius:3px;background:#e6e6e6}
.ghost-btn{position:absolute;top:586px;height:36px;border:2px solid var(--ghost-border);border-radius:3px;color:var(--ghost-text);font-size:15px;font-weight:300;display:flex;align-items:center;justify-content:center}
.modal{position:absolute;left:494px;top:185px;width:400px;height:303px;background:var(--white);border-radius:3px;box-shadow:0 6px 24px rgba(0,0,0,.18)}
.modal-info{position:absolute;left:36px;top:29px;font-size:14.4px;font-weight:300;line-height:20px;color:#333}
.download{position:absolute;left:38px;top:241px;width:157px;height:37px;border-radius:3px;background:var(--brand);color:var(--white);font-size:14.5px;font-weight:300;display:flex;align-items:center;justify-content:center}
</style>
</head>
<body>
<div class="app">
  <header class="topbar">
    <div class="brand"><span class="brand-dot"></span><span>Vantrel</span></div>
    <div class="user">
      <div class="avatar" role="img" aria-label="User profile photo"></div>
      <span class="user-name">Martin Hale</span>
      <svg class="user-caret" width="16" height="10" viewBox="0 0 16 10"><path d="M1 1l7 7 7-7" fill="none" stroke="#1f5fad" stroke-width="2.5"/></svg>
    </div>
  </header>

  <nav class="sidebar">
    <div class="nav-item" style="top:28px">Appointments</div>
    <div class="nav-item" style="top:67px">Consultation</div>
    <div class="nav-item" style="top:98px">Patient</div>
    <div class="nav-item" style="top:130px">Drugs inventory</div>
    <div class="nav-item" style="top:161px">General supplies<br>inventory</div>
    <div class="nav-item" style="top:211px">Laboratory</div>
    <div class="nav-item" style="top:242px">Suppliers</div>
    <div class="nav-item" style="top:274px">Insurance</div>
    <div class="nav-item active" style="top:298px">Reports</div>
  </nav>

  <div class="select" style="left:250px;width:426px">Select Report Type
    <svg width="16" height="10" viewBox="0 0 16 10"><path d="M1 1l7 7 7-7" fill="none" stroke="#cfdcec" stroke-width="2.5"/></svg></div>
  <div class="select" style="left:720px;width:426px">Select Date
    <svg width="16" height="10" viewBox="0 0 16 10"><path d="M1 1l7 7 7-7" fill="none" stroke="#cfdcec" stroke-width="2.5"/></svg></div>

  <div class="table">
    <div class="row"><span class="name">Pulmonary CT</span><span class="act" style="left:639px">Delete</span><span class="act" style="left:740px">Rename</span><span class="act" style="left:838px">View</span></div>
    <div class="row"><span class="name">Pulmonary CT</span><span class="act" style="left:639px">Delete</span><span class="act" style="left:740px">Rename</span><span class="act" style="left:838px">View</span></div>
    <div class="row"><span class="name">Pulmonary CT</span><span class="act" style="left:639px">Delete</span><span class="act" style="left:740px">Rename</span><span class="act" style="left:838px">View</span></div>
    <div class="row"><span class="name">Pulmonary CT</span><span class="act" style="left:639px">Delete</span><span class="act" style="left:740px">Rename</span><span class="act" style="left:838px">View</span></div>
    <div class="row"><span class="name">Pulmonary CT</span><span class="act" style="left:639px">Delete</span><span class="act" style="left:740px">Rename</span><span class="act" style="left:838px">View</span></div>
    <div class="row"><span class="name">Pulmonary CT</span><span class="act" style="left:639px">Delete</span><span class="act" style="left:740px">Rename</span><span class="act" style="left:838px">View</span></div>
    <div class="row"><span class="name">Pulmonary CT</span><span class="act" style="left:639px">Delete</span><span class="act" style="left:740px">Rename</span><span class="act" style="left:838px">View</span></div>
    <div class="row"><span class="name">Pulmonary CT</span><span class="act" style="left:639px">Delete</span><span class="act" style="left:740px">Rename</span><span class="act" style="left:838px">View</span></div>
    <div class="row"><span class="name">Pulmonary CT</span><span class="act" style="left:639px">Delete</span><span class="act" style="left:740px">Rename</span><span class="act" style="left:838px">View</span></div>
    <div class="row"><span class="name">Pulmonary CT</span><span class="act" style="left:639px">Delete</span><span class="act" style="left:740px">Rename</span><span class="act" style="left:838px">View</span></div>
    <div class="row"></div>
  </div>
  <div class="scroll"></div>

  <div class="ghost-btn" style="left:251px;width:105px">Scan</div>
  <div class="ghost-btn" style="left:370px;width:111px">Video</div>
  <div class="ghost-btn" style="left:497px;width:111px">Import</div>
  <div class="ghost-btn" style="left:624px;width:111px">Return</div>

  <div class="modal" role="dialog" aria-label="Report details">
    <div class="modal-info">
      <p>Date: 28/05/2018</p>
      <p>Report Type: Pulmonary CT</p>
      <p>Patient Name: Peter Lane</p>
      <p>Previous Reports: NILL</p>
    </div>
    <div class="download">Download Report</div>
  </div>
</div>
</body>
</html>
```